Consumer and commercial IOT solutions (Internet Of Things)

We are a startup and are looking for business cards with logo. The logo will appear on all of our media as well as our ecommerce site and social sites that have yet to be developed. We want to present a fresh face on a high tech company that innovates at every turn. You can read about our solutions on our information only web site www.plonaxhub.net - We have some wording we would like used on our business cards but there is no place for this except for here. The company name is "RM Industrial IOT" I have some samples of logos I am interested in seeing but I will let your team make the initial presentations

```html
<!DOCTYPE html>
<html lang="en">
<head>
<meta charset="utf-8">
<title>RM Industrial IOT – Business Card</title>
<link rel="stylesheet" href="https://fonts.googleapis.com/css2?family=Montserrat:wght@400;500;700&display=swap">
<style>
  :root {
    --navy: #0b2446;
    --navy-deep: #061a35;
    --navy-light: #1f4575;
    --orange: #f26a1b;
    --white: #ffffff;
    --ink: #1c2b45;
    --backdrop: #e9e6e1;
  }
  * { margin: 0; padding: 0; box-sizing: border-box; }
  html, body {
    width: 1200px; height: 900px; overflow: hidden;
    background: var(--backdrop);
    font-family: "Montserrat", sans-serif;
  }
  .canvas {
    width: 1200px; height: 900px;
    display: flex; flex-direction: column;
    align-items: center; justify-content: center; gap: 56px;
  }
  .card {
    width: 600px; height: 343px;
    border-radius: 22px;
    position: relative; overflow: hidden;
    box-shadow: 0 14px 30px rgba(0,0,0,.18);
  }

  /* Back of card */
  .card-back { background: var(--navy-deep); }
  .card-back .pattern-field {
    position: absolute; inset: 0;
    background: linear-gradient(135deg, var(--navy-deep) 0%, var(--navy) 45%, var(--navy-light) 100%);
  }
  .card-back .brand {
    position: absolute; right: 34px; top: 50%;
    transform: translateY(-50%);
    display: flex; align-items: center; gap: 10px;
  }
  .brand-dot {
    width: 14px; height: 14px; border-radius: 50%;
    background: var(--orange);
  }
  .brand-name {
    color: var(--white); font-weight: 700; font-size: 18px;
    letter-spacing: .02em;
  }

  /* Front of card */
  .card-front {
    background: var(--white);
    border-bottom: 6px solid var(--navy-deep);
  }
  .company-name {
    position: absolute; left: 46px; top: 40px;
    color: var(--navy); font-weight: 700;
    font-size: 27px; line-height: 1.12; letter-spacing: .03em;
    text-transform: uppercase;
  }
  .company-name span { display: block; }
  .company-name .indent-1 { padding-left: 14px; }
  .company-name .indent-2 { padding-left: 28px; }

  .person {
    position: absolute; left: 88px; top: 182px;
  }
  .person-name {
    font-weight: 700; font-size: 17px; letter-spacing: .02em;
    color: var(--navy); text-transform: uppercase;
  }
  .person-name .surname { color: var(--orange); }
  .person-title {
    font-weight: 400; font-size: 15px; letter-spacing: .04em;
    color: var(--ink); text-transform: uppercase; margin-top: 2px;
  }
  .contact-list {
    list-style: none; margin-top: 18px;
  }
  .contact-list li {
    display: flex; align-items: center; gap: 10px;
    font-size: 15px; color: var(--ink); line-height: 1.55;
  }
  .contact-icon {
    width: 15px; height: 15px; border-radius: 3px;
    background: var(--orange);
    display: inline-flex; align-items: center; justify-content: center;
    flex: none;
  }
  .contact-icon svg { width: 11px; height: 11px; }
</style>
</head>
<body>
  <main class="canvas">
    <section class="card card-back" aria-label="Business card, back">
      <div class="pattern-field" role="img" aria-label="Repeating tiled brand pattern on deep navy"></div>
      <div class="brand">
        <span class="brand-dot"></span>
        <span class="brand-name">RM Industrial IOT</span>
      </div>
    </section>

    <section class="card card-front" aria-label="Business card, front">
      <h1 class="company-name">
        <span>RM</span>
        <span class="indent-1">Industrial</span>
        <span class="indent-2">IOT</span>
      </h1>

      <div class="person">
        <p class="person-name">Marcus <span class="surname">Delane</span></p>
        <p class="person-title">Co-Founder &amp; CEO</p>
        <ul class="contact-list">
          <li>
            <span class="contact-icon">
              <svg viewBox="0 0 24 24" fill="#fff"><path d="M6.6 10.8a15.1 15.1 0 0 0 6.6 6.6l2.2-2.2a1 1 0 0 1 1-.25 11.4 11.4 0 0 0 3.6.57 1 1 0 0 1 1 1V20a1 1 0 0 1-1 1A17 17 0 0 1 3 4a1 1 0 0 1 1-1h3.5a1 1 0 0 1 1 1c0 1.25.2 2.45.57 3.57a1 1 0 0 1-.25 1z"/></svg>
            </span>
            0491570186
          </li>
          <li>
            <span class="contact-icon">
              <svg viewBox="0 0 24 24" fill="none" stroke="#fff" stroke-width="2.4"><rect x="3" y="5" width="18" height="14" rx="2"/><path d="M3 7l9 6 9-6"/></svg>
            </span>
            info@plonaxhub.com
          </li>
          <li>
            <span class="contact-icon">
              <svg viewBox="0 0 24 24" fill="none" stroke="#fff" stroke-width="2.2"><circle cx="12" cy="12" r="9"/><path d="M3 12h18M12 3c3 3.2 3 14.8 0 18M12 3c-3 3.2-3 14.8 0 18"/></svg>
            </span>
            www.plonaxhub.net
          </li>
        </ul>
      </div>
    </section>
  </main>
</body>
</html>
```